Commercial Real Estate Corporate Site

Our company sells an ERP software to Commercial Real Estate Companies, this project is part of a marketing and sales relaunch of the company.

See attached for PDF formatted Design brief

The software is a modular system where client’s can adopt one module at a time. Our customers are corporate clients who own between 10M and 10B of real estate properties. The typical customer is from the IT or the Financial arm of the company. Our differentiation in the market is that our system is built on a no-code environment, so making changes for the client is quick. Incumbents in the market have long implementation cycles, and customization is often not possible. Competitors are Quorvel, TKB, PlotNest, Vumora.

We need a design for our site which will be implemented into Brevo Forge. **All designs must be compatible with the newest version of Brevo Forge.**

We have produced the following attached assets to use in the website design.:

1. Logo
2. Brand Guidelines
3. Content for Pages
4. Menu Structures
5. Illustrations (modules)
I can't attach them because the files are too big, so they're in this google drive instead:
https://files.examplestore.net/share/k29Xa7Lq0Pz3Rt8MwB5nYc4Hv1Jd6Fe?mode=view

The mechanic for our sales process is as follows:

1. We find on module from our application that a client is interested in. The illustrations that we’ve attached represent the individual modules (elements) of the software.
1. For instance, one of our current customers has purchased a commissions module from us which helps calculate the commission that brokers receive for buying and selling their properties.
2. We provide immense value through the module, and then keep in sales communication with the client to determine which other modules we can implement for them.
1. For instance, in the example above, the client is so happy with the commissions module that they want to start working with our leasing module as well. In the next business quarter, they also choose to add our financials module to their business systems.

### Logo

Attached

### Brand Guidelines

Attached

We are open to suggestions on the secondary colour palette.

### **Site Copy**

**We require the following pages to be created; For now, we will do one Market Page, one Product Page, and one Platform / Services Page, and we will use those as inspiration to create the other dozen Marketing Pages and 30 or so Product Pages.**

**Homepage**

Attached

**Market Page** - look at the quorvel site under the Office, Industrial, Retail (https://www.quorvel.com/products/quorvel-commercial-suite/)

**Product** - One product provided, but there will be 30 - look at the vumora page

(https://www.vumora.com/products/general-accounting)

**Platform / Services Page** - pages that tell the story of our platform and services, content to be provided - the platform will use our modules as it highlights the story of the configurability and composability of the platform. Instead of the icons that they use, we want to use our modules.

- https://www.pelbrix.com/enterprise-applications-platform
- https://www.pelbrix.com/cloud-architecture

**Team Page** - just add sample content for starters (6 Team Members to start)

**Schedule Demo Page** - the call to action for all pages

(https://go.vumora.com/schedule-demo.html)

### Menu Structure

The menu is provided as an attachment.

### Illustrations Information

A note about the illustrations - we have provided an illustrator file with the modules, and if you’d like you can arrange the in any way that you’d like to. We especially like when the modules are positioned like a periodic table of the elements.

Our existing clients are

- Torvane Coop - https://www.torvanecoop.com/real-estate/
- Dalsworth Realestate https://dalsworth.com

Our competitors are

- Quorvel - www.quorvel.com
- TKB - [www.tkbsoftware.com](https://www.tkbsoftware.com/) (we don’t like how this one looks)
- Vumora - www.vumora.com
- Plotnest - www.plotnest.com

Design inspiration

- https://lark-studio.brevosite.com/velmo
- Corporate
- Established
- Modern

### Stock Images Guidance

- https://www.drafta.net/design/QXR7Lm2TpWz/Hk9vN3c8Yd41-FbqsaZRr/edit?utm_content=QXR7Lm2TpWz&utm_campaign=designshare&utm_medium=link2&utm_source=sharebutton

Target Market(s)

Commercial Real Estate Companies - they typically own a portfolio of 50 - 5000 real estate properties and need a software to manage it all.

Coding

Coded - Design and coding required

Number of Pages Required

5+ page

Font styles to use
Other font styles liked:
• Fonts defined in brand guideline

Requirements
Must have
• Brevo Forge, Use the Elemental Design, Download ai.zip and png.zip Use Brand Guideline,
Nice to have
• Check design breif

```html
<!DOCTYPE html>
<html lang="en">
<head>
<meta charset="utf-8">
<title>Domvera – Enterprise Applications Platform for Real Estate</title>
<link href="https://fonts.googleapis.com/css2?family=Montserrat:wght@400;500;600;700&family=Mulish:wght@400;500;600;700&family=Russo+One&display=swap" rel="stylesheet">
<style>
  :root {
    --red: #e3141b;
    --deep-red: #9a0a0f;
    --white: #ffffff;
    --soft-white: #e9e9e9;
    --grey: #8a8a8a;
    --footer-black: #000000;
    --head-font: "Montserrat", sans-serif;
    --body-font: "Mulish", sans-serif;
    --display-font: "Russo One", sans-serif;
  }
  * { box-sizing: border-box; margin: 0; padding: 0; }
  html, body { width: 1200px; height: 4211px; overflow: hidden; }
  body { position: relative; font-family: var(--body-font); color: var(--white); background: var(--footer-black); }
  .abs { position: absolute; }
  .lines { white-space: nowrap; }

  /* Hero */
  .hero {
    position: absolute; left: 0; top: 0; width: 1200px; height: 785px;
    background:
      radial-gradient(ellipse at 55% 35%, rgba(120,130,145,.35), transparent 60%),
      linear-gradient(180deg, #2c323b 0%, #1b1f25 70%, #15181d 100%);
  }
  .brand { display: flex; align-items: center; gap: 16px; }
  .brand-square { width: 52px; height: 52px; background: var(--red); }
  .brand-name { font-family: var(--head-font); font-weight: 700; color: var(--red); letter-spacing: 2px; }
  .hero .brand { left: 67px; top: 50px; }
  .hero .brand-name { font-size: 60px; line-height: 84px; }
  .menu-button {
    left: 1077px; top: 0; width: 123px; height: 123px; background: var(--grey);
    display: flex; flex-direction: column; justify-content: center; align-items: center; gap: 12px;
  }
  .menu-button span { display: block; width: 58px; height: 6px; background: var(--white); border-radius: 3px; }
  .welcome { left: 67px; top: 232px; font-family: var(--head-font); font-size: 33px; font-weight: 600; letter-spacing: 1px; display: flex; align-items: center; gap: 30px; }
  .welcome::after { content: ""; display: block; width: 443px; height: 3px; background: var(--white); }
  .hero-title { left: 67px; top: 312px; font-family: var(--head-font); font-size: 96px; font-weight: 700; color: var(--soft-white); line-height: 110px; }
  .tagline { left: 67px; top: 447px; font-family: var(--head-font); font-size: 37px; font-weight: 600; line-height: 54px; }
  .button { height: 89px; font-family: var(--head-font); font-size: 33px; font-weight: 600; display: flex; align-items: center; justify-content: center; border-radius: 6px; }
  .button-primary { left: 67px; top: 592px; width: 337px; background: var(--red); }
  .button-outline { left: 449px; top: 592px; width: 336px; border: 3px solid var(--white); }

  /* Intro */
  .intro {
    position: absolute; left: 0; top: 785px; width: 1200px; height: 2243px;
    background:
      radial-gradient(ellipse at 60% 40%, rgba(95,95,100,.45), transparent 55%),
      radial-gradient(ellipse at 40% 78%, rgba(80,80,85,.4), transparent 50%),
      linear-gradient(180deg, #2e2f32 0%, #26272a 60%, #1d1e20 100%);
  }
  .section-title { left: 67px; top: 875px; font-family: var(--head-font); font-size: 96px; font-weight: 700; color: var(--soft-white); line-height: 100px; }
  .photo-frame { background: var(--deep-red); }
  .photo { border-radius: 18px; }
  .photo-professional { left: 95px; top: 1007px; width: 404px; height: 448px;
    background: linear-gradient(160deg, #5a6b80 0%, #d8cf9a 55%, #33404f 100%); }
  .photo-developer { left: 698px; top: 1660px; width: 404px; height: 443px;
    background: linear-gradient(160deg, #c9b79a 0%, #8c6e63 50%, #4a3a44 100%); }
  .body-text { font-size: 34px; line-height: 56px; }
  .intro-text-one { left: 572px; top: 990px; }
  .intro-text-two { left: 95px; top: 1708px; font-size: 33px; }
  .about-title { left: 0; top: 2330px; width: 1200px; text-align: center; font-family: var(--display-font); font-size: 100px; line-height: 110px; }
  .about-title .accent { color: var(--red); }
  .about-text { left: 67px; top: 2494px; font-size: 35px; line-height: 56px; }

  /* Footer */
  .footer-brand { left: 76px; top: 3200px; gap: 14px; }
  .footer-brand .brand-square { width: 70px; height: 70px; }
  .footer-brand .brand-name { font-size: 62px; line-height: 90px; }
  .social { left: 174px; top: 3382px; display: flex; gap: 38px; }
  .social span { display: block; width: 73px; height: 73px; background: var(--white); border-radius: 14px; }
  .footer-heading { font-family: var(--head-font); font-size: 37px; font-weight: 500; letter-spacing: 1px; padding-bottom: 8px; border-bottom: 4px solid var(--white); line-height: 48px; }
  .footer-list { list-style: none; font-size: 33px; line-height: 64.5px; white-space: nowrap; }
  .support-heading { left: 67px; top: 3616px; }
  .support-list { left: 67px; top: 3686px; }
  .sitemap-heading { left: 735px; top: 3156px; }
  .sitemap-list { left: 735px; top: 3224px; font-weight: 700; }
  .sitemap-list li:first-child { font-weight: 500; }
  .siteinfo-heading { left: 735px; top: 3756px; }
  .siteinfo-list { left: 735px; top: 3823px; }
</style>
</head>
<body>

<header class="hero">
  <div class="abs brand"><span class="brand-square"></span><span class="brand-name">DOMVERA</span></div>
  <div class="abs menu-button" aria-label="Menu"><span></span><span></span><span></span></div>
  <p class="abs welcome">WELCOME TO</p>
  <h1 class="abs hero-title">Domvera</h1>
  <p class="abs tagline lines">An infinitely composable Enterprise<br>Applications Platform (EAP) for real estate.</p>
  <a class="abs button button-primary">GET STARTED</a>
  <a class="abs button button-outline">LEARN MORE</a>
</header>

<main>
  <section class="intro"></section>
  <h2 class="abs section-title">Domvera</h2>

  <div class="abs photo-frame" style="left:67px;top:1051px;width:404px;height:444px;"></div>
  <div class="abs photo photo-professional" role="img" aria-label="Smiling businesswoman in a yellow blazer in an office"></div>
  <p class="abs body-text intro-text-one lines">Far beyond what’s possible with<br>tired, legacy real estate ERP<br>software, Domvera offers a<br>complete industry solution,<br>architected as flexible modules<br>that can be assembled and<br>configured into an infinite<br>combination of processes and<br>workflows.</p>

  <div class="abs photo-frame" style="left:729px;top:1705px;width:404px;height:446px;"></div>
  <div class="abs photo photo-developer" role="img" aria-label="Smiling man with glasses working at a laptop"></div>
  <p class="abs body-text intro-text-two lines">The Domvera Enterprise<br>solution seamlessly delivers<br>both modular software and<br>bundled services to transform<br>your business with less risk,<br>greater security, and lower cost.</p>

  <h2 class="abs about-title"><span class="accent">ABOUT</span> US</h2>
  <p class="abs about-text lines">Domvera is the real estate industry’s modern alternative to<br>rigid, legacy ERP systems. With decades of real estate<br>enterprise software development and implementation<br>expertise — spanning hundreds of blue chip global real estate<br>investment firms — we have a proven track record of<br>enterprise excellence.</p>
</main>

<footer>
  <div class="abs brand footer-brand"><span class="brand-square"></span><span class="brand-name">DOMVERA</span></div>
  <div class="abs social">
    <span role="img" aria-label="Social profile one"></span>
    <span role="img" aria-label="Social profile two"></span>
    <span role="img" aria-label="Social profile three"></span>
  </div>

  <h3 class="abs footer-heading support-heading">SUPPORT</h3>
  <ul class="abs footer-list support-list">
    <li>Customer Support</li>
    <li>Purchase Orders &amp; Payment Terms</li>
    <li>Technical Assistance</li>
    <li>FAQs</li>
    <li>Contact Us</li>
  </ul>

  <h3 class="abs footer-heading sitemap-heading">SITE MAP</h3>
  <ul class="abs footer-list sitemap-list">
    <li>Home</li>
    <li>Markets</li>
    <li>Products</li>
    <li>Platform</li>
    <li>Services</li>
    <li>Resources</li>
    <li>About</li>
  </ul>

  <h3 class="abs footer-heading siteinfo-heading">SITE INFORMATION</h3>
  <ul class="abs footer-list siteinfo-list">
    <li>Privacy Policy</li>
    <li>Terms of Service</li>
    <li>Accessibility Statement</li>
    <li>Compliance</li>
  </ul>
</footer>

</body>
</html>
```